Laser Tattoo Removal Business Cards

We are looking for a professional business card design for a laser tattoo removal business. Ideally looking for a black business card design. The name of the business is Brightline Tattoo Removal. We place our cards at local tattoo shops so we ideally are looking for something trendy/edgy to draw both male and female clientele in.

Target Market(s)

Male/Female ages 18-60

Contact Information for Business Card

black background ideally.. hoping to stay within greys, whites and black

Font styles to use
Serif
Sans Serif

Colors
121212
a9a9a9
5c5c5c
f5f5f5
ffffff
7f7f7f
606060
848484
9d9d9d

Requirements
Must have
• Employee Info:
• Melissa Thornbury
• Chief Executive Offer
• m: 919.537.2846
• w: 919.362.4178
• f: 919.685.3907
• mthornbury@brightlinetattooremoval.example
• Address:
• 4615 Oakmere Pkwy, Suite 210
• Raleigh, NC 27654
• Website:
• www.brightlinetattooremoval.example
Nice to have
• Myabe business name on back or logo on back and employee info on the front

```html
<!DOCTYPE html>
<html lang="en">
<head>
<meta charset="utf-8">
<title>Brightline Tattoo Removal – Business Cards</title>
<link rel="stylesheet" href="https://fonts.googleapis.com/css2?family=Montserrat:wght@400;500;600&display=swap">
<style>
  :root {
    --ink: #121212;
    --grey-dark: #5c5c5c;
    --grey-mid: #7f7f7f;
    --grey-soft: #a9a9a9;
    --paper: #ffffff;
    --mist: #f5f5f5;
    --stage: #dcdcdc;
  }
  * { box-sizing: border-box; margin: 0; padding: 0; }
  html, body { width: 1200px; height: 960px; overflow: hidden; }
  body {
    background: var(--stage);
    font-family: "Montserrat", Arial, sans-serif;
    color: var(--ink);
    position: relative;
  }
  .card {
    position: absolute;
    left: 272px;
    width: 656px;
    height: 374px;
    background: var(--paper);
    border-radius: 22px;
    overflow: hidden;
    box-shadow: 0 6px 18px rgba(0,0,0,0.18);
  }
  .card--front { top: 80px; }
  .card--back { top: 506px; }

  .brand {
    position: absolute;
    top: 46px;
    right: 40px;
    width: 190px;
    text-align: center;
    font-weight: 500;
    color: var(--ink);
    z-index: 2;
  }
  .brand__name { font-size: 29px; letter-spacing: 2px; line-height: 1; }
  .brand__tagline { font-size: 13px; letter-spacing: 3.2px; margin-top: 12px; }

  .person { position: absolute; left: 38px; top: 146px; }
  .person__name { font-size: 22px; font-weight: 600; letter-spacing: 0.3px; color: #222; }
  .person__title { font-size: 16.5px; font-weight: 400; color: var(--grey-dark); margin-top: 5px; }

  .divider {
    position: absolute; left: 39px; right: 35px; top: 217px;
    height: 1px; background: var(--grey-soft);
  }

  .contact { position: absolute; left: 38px; top: 243px; list-style: none; }
  .contact li {
    display: flex; align-items: center; gap: 8px;
    font-size: 14.5px; color: var(--grey-dark); height: 22px;
  }
  .contact svg { width: 11px; height: 11px; fill: var(--ink); flex: none; }

  .address {
    position: absolute; right: 35px; top: 243px;
    font-style: normal; text-align: right;
    font-size: 14.5px; line-height: 22px; color: var(--grey-dark);
  }

  .swoosh { position: absolute; left: 0; bottom: 0; width: 656px; height: 60px; }
  .website {
    position: absolute; right: 35px; bottom: 7px;
    font-size: 14.5px; color: var(--paper); letter-spacing: 0.2px;
  }

  .photo-area {
    position: absolute; left: 0; right: 0; top: 118px; bottom: 0;
    background: linear-gradient(180deg, rgba(245,245,245,0.9) 0%, #c9c9c9 30%, #8a8a8a 60%, #3a3a3a 85%, #1e1e1e 100%);
  }
</style>
</head>
<body>

<section class="card card--front" aria-label="Business card front">
  <div class="brand">
    <div class="brand__name">BRIGHTLINE</div>
    <div class="brand__tagline">TATTOO REMOVAL</div>
  </div>

  <div class="person">
    <h1 class="person__name">MELISSA THORNBURY</h1>
    <p class="person__title">Chief Executive Offer</p>
  </div>

  <div class="divider"></div>

  <ul class="contact">
    <li><svg viewBox="0 0 12 12" aria-hidden="true"><path d="M3 0h6a1 1 0 0 1 1 1v10a1 1 0 0 1-1 1H3a1 1 0 0 1-1-1V1a1 1 0 0 1 1-1zm.6 1.5v8h4.8v-8z"/></svg>919.537.2846</li>
    <li><svg viewBox="0 0 12 12" aria-hidden="true"><path d="M9.5 0.5 11 2.3c.3.4.2.9-.2 1.1L9.3 4.2C8.4 2.8 6 3.6 4.6 6.3 3.2 9 4 10.6 5 10.8l-.5 1a1 1 0 0 1-1 .1C1.7 11 .9 8.4 2.5 5.3 4 2.3 6.8.3 9.5.5z"/></svg>919.362.4178</li>
    <li><svg viewBox="0 0 12 12" aria-hidden="true"><path d="M3 0h6v3H3zM1 4h10a1 1 0 0 1 1 1v4H10v3H2V9H0V5a1 1 0 0 1 1-1zm2.5 4.5v2h5v-2z"/></svg>919.685.3907</li>
    <li><svg viewBox="0 0 12 12" aria-hidden="true"><path d="M0 2.5h12v7H0zm1.2 1 4.8 3.3 4.8-3.3z"/></svg>mthornbury@brightlinetattooremoval.example</li>
  </ul>

  <address class="address">
    4615 Oakmere Pkwy, Suite 210<br>
    Raleigh, NC 27654
  </address>

  <svg class="swoosh" viewBox="0 0 656 60" aria-hidden="true">
    <path d="M120 60 Q380 18 656 22 L656 28 Q400 26 150 60 Z" fill="#9d9d9d"/>
    <path d="M150 60 Q400 30 656 28 L656 60 Z" fill="#121212"/>
  </svg>
  <span class="website">www.brightlinetattooremoval.example</span>
</section>

<section class="card card--back" aria-label="Business card back">
  <div class="photo-area" role="img" aria-label="Photo of a technician performing laser tattoo removal on a client's tattoo, fading from white into black"></div>
  <div class="brand">
    <div class="brand__name">BRIGHTLINE</div>
    <div class="brand__tagline">TATTOO REMOVAL</div>
  </div>
</section>

</body>
</html>
```